Business Card Design (NEW FILES)

ATTENTION: New vector files are available. Please update your design to reflect/use the new (better resolution) logo images.

Seeking a unique and professional business card design for a commercial drone photography/videography business. The layout should feature
the logo (attached) and include the following information:
Owen Tarrick
614-502-7738
www.skylarkreelworks.example
NRD Certified Remote Pilot

Owen Tarrick

```html
<!DOCTYPE html>
<html lang="en">
<head>
<meta charset="utf-8">
<title>Skylark Reelworks – Business Card</title>
<link href="https://fonts.googleapis.com/css2?family=Open+Sans:wght@400;600;700&display=swap" rel="stylesheet">
<style>
  :root {
    --backdrop: #222222;
    --navy: #1a1c4b;
    --navy-deep: #14173f;
    --paper: #ffffff;
    --orange: #ec8a4a;
    --ink-light: #ffffff;
  }
  html, body {
    margin: 0;
    padding: 0;
    width: 1200px;
    height: 780px;
    overflow: hidden;
    background: var(--backdrop);
    font-family: "Open Sans", Arial, sans-serif;
  }
  .canvas {
    position: relative;
    width: 1200px;
    height: 780px;
  }
  .card {
    position: absolute;
    top: 240px;
    width: 525px;
    height: 300px;
    overflow: hidden;
    box-shadow: 0 18px 40px rgba(0,0,0,0.45);
  }
  /* Front */
  .card-front {
    left: 50px;
    background: var(--navy);
  }
  .brand-band {
    position: absolute;
    left: 0; top: 0;
    width: 150px;
    height: 100%;
    background: var(--paper);
    display: flex;
    align-items: center;
    justify-content: center;
  }
  .brand-band .wordmark {
    transform: rotate(-90deg);
    white-space: nowrap;
    display: flex;
    align-items: center;
    gap: 10px;
    font-size: 22px;
    font-weight: 400;
    letter-spacing: 1px;
    color: var(--navy);
    text-transform: uppercase;
  }
  .mark-dot {
    display: inline-block;
    width: 14px;
    height: 14px;
    border-radius: 50%;
    background: var(--orange);
  }
  .contact {
    position: absolute;
    right: 38px;
    bottom: 26px;
    text-align: right;
    color: var(--ink-light);
  }
  .contact .name {
    margin: 0;
    font-size: 30px;
    font-weight: 700;
    line-height: 1.05;
  }
  .contact .name .first { color: var(--orange); font-weight: 600; }
  .contact .role {
    margin: 2px 0 14px;
    font-size: 15px;
  }
  .contact .line {
    margin: 0;
    font-size: 15px;
    line-height: 1.45;
  }
  .contact .icon-line {
    display: flex;
    justify-content: flex-end;
    align-items: center;
    gap: 8px;
  }
  .contact svg { width: 14px; height: 14px; }
  .accent-tab {
    position: absolute;
    right: 0;
    top: 132px;
    width: 22px;
    height: 48px;
    background: var(--orange);
  }
  /* Back */
  .card-back {
    left: 625px;
    background: var(--navy-deep);
    display: flex;
    align-items: center;
    justify-content: center;
  }
  .card-back .wordmark {
    display: flex;
    align-items: center;
    gap: 14px;
    font-size: 34px;
    font-weight: 400;
    letter-spacing: 2px;
    color: var(--ink-light);
    text-transform: uppercase;
  }
  .card-back .mark-dot { width: 20px; height: 20px; }
</style>
</head>
<body>
<main class="canvas">
  <section class="card card-front" aria-label="Business card front">
    <div class="brand-band">
      <div class="wordmark"><span>Skylark Reelworks</span><span class="mark-dot"></span></div>
    </div>
    <div class="accent-tab"></div>
    <div class="contact">
      <h1 class="name"><span class="first">Owen</span> Tarrick</h1>
      <p class="role">Owner</p>
      <p class="line">NRD Certified Remote Pilot</p>
      <p class="line">Fully Insured</p>
      <p class="line icon-line">614-502-7738
        <svg viewBox="0 0 24 24" aria-hidden="true"><path fill="#ec8a4a" d="M6.6 10.8a15.1 15.1 0 0 0 6.6 6.6l2.2-2.2a1 1 0 0 1 1-.25 11.4 11.4 0 0 0 3.6.57 1 1 0 0 1 1 1V20a1 1 0 0 1-1 1A17 17 0 0 1 3 4a1 1 0 0 1 1-1h3.5a1 1 0 0 1 1 1c0 1.25.2 2.45.57 3.57a1 1 0 0 1-.25 1z"/></svg>
      </p>
      <p class="line icon-line">www.skylarkreelworks.example
        <svg viewBox="0 0 24 24" aria-hidden="true"><circle cx="12" cy="12" r="10" fill="none" stroke="#ec8a4a" stroke-width="2"/><path d="M2 12h20M12 2a15 15 0 0 1 0 20M12 2a15 15 0 0 0 0 20" fill="none" stroke="#ec8a4a" stroke-width="1.6"/></svg>
      </p>
    </div>
  </section>

  <section class="card card-back" aria-label="Business card back">
    <div class="wordmark"><span>Skylark Reelworks</span><span class="mark-dot"></span></div>
  </section>
</main>
</body>
</html>
```